Modern Business Card for Larkwell 2018

Our company assumes the best about people. We are creating an online community of entrepreneurs and business leaders who struggle with marketing their business online.

This business card should POP! We recently got a new logo and are launching a new website next month, so our business cards should make a statement that feels:
-Fresh
-Smart
-Trustworthy
-Fun

Target Market(s)

small business owners, entrepreneurs

Industry/Entity Type

Digital Marketing

Contact Information for Business Card

Dimensions: 3.5" x 2"

Font styles to use
Sans Serif

Colors
f37122
ffffff

Requirements
Must have
• We need a business card with a modern, bold design. We will use one side of the card as a lead-generation offer, so text on one side will need to fit up to 140 characters. The business card should stick to our core colors (orange, black, and white).
Nice to have
• We think a vertical "portrait" design could be interesting.
Should not have
• Should not look like a traditional business card. The round icon should stand out from a distance.

```html
<!DOCTYPE html>
<html lang="en">
<head>
<meta charset="utf-8">
<title>Larkwell Business Card</title>
<link rel="stylesheet" href="https://fonts.googleapis.com/css2?family=Montserrat:wght@700&family=Permanent+Marker&family=Open+Sans:wght@600&family=Fira+Mono:wght@700&family=Roboto:wght@700&family=Kalam:wght@400&display=swap">
<style>
  :root {
    --backdrop: #2b2b2b;
    --orange: #ec5a0a;
    --orange-light: #f37122;
    --white: #ffffff;
  }
  html, body {
    margin: 0;
    padding: 0;
    width: 1200px;
    height: 1200px;
    overflow: hidden;
    background: var(--backdrop);
  }
  .canvas {
    position: relative;
    width: 1200px;
    height: 1200px;
  }
  .card {
    position: absolute;
    top: 150px;
    width: 480px;
    height: 840px;
  }
  .card-front { left: 100px; }
  .card-back { left: 646px; }
  .card svg { display: block; }
  .role-title {
    font-family: 'Montserrat', sans-serif;
    font-weight: 700;
    font-size: 16px;
  }
  .person-name {
    font-family: 'Permanent Marker', cursive;
    font-size: 46px;
  }
  .email {
    font-family: 'Montserrat', sans-serif;
    font-weight: 700;
    font-size: 20px;
  }
  .brand-small {
    font-family: 'Montserrat', sans-serif;
    font-weight: 700;
    font-size: 14px;
    letter-spacing: 3px;
  }
  .benefit {
    font-family: 'Open Sans', sans-serif;
    font-weight: 600;
    font-size: 22px;
    letter-spacing: 2.2px;
  }
  .offer {
    font-family: 'Fira Mono', monospace;
    font-weight: 700;
    font-size: 18.5px;
  }
  .url {
    font-family: 'Roboto', sans-serif;
    font-weight: 700;
    font-size: 25px;
  }
  .brand-large {
    font-family: 'Roboto', sans-serif;
    font-weight: 700;
    font-size: 36px;
  }
  .tagline {
    font-family: 'Kalam', cursive;
    font-size: 21px;
  }
</style>
</head>
<body>
<div class="canvas">

  <!-- Front: name side -->
  <div class="card card-front">
    <svg width="480" height="840" viewBox="0 0 480 840" xmlns="http://www.w3.org/2000/svg">
      <rect class="card-paper" x="0" y="0" width="480" height="840" fill="var(--white)"/>
      <rect class="stamp-field" x="10" y="16" width="460" height="812" fill="var(--orange)"/>
      <rect class="stamp-teeth" x="12" y="18" width="456" height="808" fill="none"
            stroke="var(--white)" stroke-width="5" stroke-dasharray="3 4"/>
      <rect class="inner-frame" x="34" y="38" width="414" height="760" rx="8"
            fill="none" stroke="var(--white)" stroke-width="8"/>

      <text class="role-title" x="240" y="372" text-anchor="middle" fill="var(--white)">STORY MARKETING COACH</text>
      <text class="person-name" x="240" y="430" text-anchor="middle" fill="var(--white)">DANA WHITFIELD</text>

      <rect class="email-box" x="86" y="452" width="304" height="32" rx="5"
            fill="none" stroke="var(--white)" stroke-width="2.5"/>
      <text class="email" x="238" y="475" text-anchor="middle" fill="var(--white)">dana@larkwellnow.com</text>

      <text class="brand-small" x="240" y="530" text-anchor="middle" fill="var(--white)">LARKWELL</text>
    </svg>
  </div>

  <!-- Back: offer side -->
  <div class="card card-back">
    <svg width="480" height="840" viewBox="0 0 480 840" xmlns="http://www.w3.org/2000/svg">
      <rect class="card-paper" x="0" y="0" width="480" height="840" fill="var(--white)"/>
      <path class="top-band" d="M0 0 H480 V152 Q300 268 0 244 Z" fill="var(--orange-light)"/>
      <path class="top-band-stripe" d="M0 262 Q300 286 480 166" fill="none" stroke="var(--orange-light)" stroke-width="6"/>

      <!-- benefit icons -->
      <g class="icon-people" fill="var(--white)">
        <circle cx="62" cy="48" r="4.5"/><circle cx="51" cy="58" r="4"/><circle cx="73" cy="58" r="4"/>
        <rect x="44" y="64" width="14" height="8" rx="3"/><rect x="66" y="64" width="14" height="8" rx="3"/>
      </g>
      <g class="icon-money">
        <circle cx="62" cy="107" r="10" fill="none" stroke="var(--white)" stroke-width="3"/>
        <text x="62" y="112" text-anchor="middle" fill="var(--white)" font-family="Roboto, sans-serif" font-weight="700" font-size="13">$</text>
        <rect x="46" y="121" width="32" height="9" rx="3" fill="var(--white)"/>
      </g>
      <g class="icon-impact" fill="var(--white)">
        <circle cx="62" cy="164" r="6"/><circle cx="53" cy="178" r="6"/><circle cx="71" cy="178" r="6"/>
      </g>

      <text class="benefit" x="113" y="70" fill="var(--white)">REACH MORE PEOPLE</text>
      <text class="benefit" x="113" y="125" fill="var(--white)">MAKE MORE MONEY</text>
      <text class="benefit" x="113" y="180" fill="var(--white)">CREATE MORE IMPACT</text>

      <!-- offer box -->
      <rect class="offer-box" x="52" y="331" width="404" height="94" rx="4"
            fill="none" stroke="var(--orange)" stroke-width="6"/>
      <line x1="389" y1="331" x2="389" y2="425" stroke="var(--orange)" stroke-width="6"/>
      <text class="offer" fill="var(--orange)">
        <tspan x="79" y="359">Get your free Larkwell</tspan>
        <tspan x="79" y="383">Starter Package and our</tspan>
        <tspan x="79" y="407">marketing guide today at</tspan>
      </text>
      <path class="offer-arrow" d="M401 357 H427 V388" fill="none" stroke="var(--orange)" stroke-width="6"/>
      <path d="M414 384 H440 L427 412 Z" fill="var(--orange)"/>

      <!-- url pill -->
      <rect class="url-pill" x="44" y="460" width="416" height="65" rx="32.5" fill="var(--orange)"/>
      <text class="url" x="252" y="502" text-anchor="middle" fill="var(--white)">LARKWELLNOW.COM/START</text>

      <!-- serrated bottom band -->
      <path class="bottom-band" d="M0 650 L480 586 V840 H0 Z" fill="var(--orange)"/>
      <line class="bottom-teeth" x1="0" y1="643" x2="480" y2="579" stroke="var(--orange)" stroke-width="14" stroke-dasharray="2.5 4.5"/>

      <circle class="brand-circle" cx="242" cy="696" r="36" fill="none" stroke="var(--white)" stroke-width="9"/>
      <text class="brand-large" x="242" y="778" text-anchor="middle" fill="var(--white)">LARKWELL</text>
      <text class="tagline" x="248" y="811" text-anchor="middle" fill="var(--white)">Tell Stories that inspire action</text>
    </svg>
  </div>

</div>
</body>
</html>
```